Create a memorable Stationary for Security Software Company

Velbrantix is the worldwide leader in securing the Internet. Making Internet communications and critical data secure, reliable and available everywhere has been and continues to be our ongoing vision. We are committed to staying focused on real customer needs and to developing new and innovative security solutions that redefine the security landscape.

Industry/Entity Type

Internet

Font styles to use
Serif
Sans Serif
Script

Colors
0792cd
33a6d7
85cae6

```html
<!DOCTYPE html>
<html lang="en">
<head>
<meta charset="utf-8">
<title>Velbrantix Business Card</title>
<link href="https://fonts.googleapis.com/css2?family=Open+Sans:wght@400;600;700&display=swap" rel="stylesheet">
<style>
  :root {
    --blue-deep: #0792cd;
    --blue-mid: #33a6d7;
    --blue-light: #85cae6;
    --ink: #3a3a3a;
    --paper: #ffffff;
    --backdrop: #eef1f3;
  }
  html, body {
    margin: 0;
    padding: 0;
    overflow: hidden;
  }
  body {
    width: 1200px;
    height: 1120px;
    background: var(--backdrop);
    position: relative;
    font-family: "Open Sans", sans-serif;
  }
  .card {
    position: absolute;
    width: 760px;
    height: 434px;
    overflow: hidden;
    box-shadow: 0 10px 30px rgba(0,0,0,0.18);
  }
  /* Card back */
  .card-back {
    left: 120px;
    top: 60px;
    background: var(--blue-light);
  }
  .brand {
    display: flex;
    align-items: center;
    gap: 16px;
    color: var(--blue-mid);
    font-weight: 700;
  }
  .brand-dot {
    border-radius: 50%;
    background: var(--blue-mid);
    flex: none;
  }
  .card-back .brand {
    position: absolute;
    left: 0;
    right: 0;
    top: 150px;
    justify-content: center;
    font-size: 56px;
    color: var(--blue-deep);
  }
  .card-back .brand-dot {
    width: 44px;
    height: 44px;
    background: var(--blue-deep);
  }
  .back-url {
    position: absolute;
    left: 0;
    right: 0;
    top: 300px;
    text-align: center;
    font-size: 22px;
    letter-spacing: 4px;
    color: var(--ink);
  }
  /* Card front */
  .card-front {
    left: 320px;
    top: 620px;
    background: var(--paper);
  }
  .card-front .brand {
    position: absolute;
    left: 70px;
    top: 150px;
    font-size: 44px;
  }
  .card-front .brand-dot {
    width: 36px;
    height: 36px;
  }
  .person {
    position: absolute;
    right: 36px;
    top: 34px;
    text-align: right;
  }
  .person-name {
    color: var(--blue-deep);
    font-weight: 700;
    font-size: 24px;
    line-height: 1.15;
  }
  .person-title {
    color: var(--ink);
    font-size: 20px;
  }
  .wave {
    position: absolute;
    left: 0;
    top: 0;
  }
  .contact {
    position: absolute;
    right: 30px;
    top: 190px;
    list-style: none;
    margin: 0;
    padding: 0;
    text-align: right;
    color: var(--paper);
    font-size: 17px;
    line-height: 30px;
  }
  .contact li {
    display: flex;
    justify-content: flex-end;
    align-items: center;
    gap: 8px;
  }
  .contact svg {
    width: 14px;
    height: 14px;
    fill: var(--paper);
  }
  .address {
    position: absolute;
    right: 30px;
    top: 366px;
    color: var(--paper);
    font-size: 17px;
    display: flex;
    align-items: center;
    gap: 8px;
  }
  .address svg {
    width: 16px;
    height: 16px;
    fill: var(--paper);
  }
</style>
</head>
<body>

<section class="card card-back">
  <div class="brand"><span class="brand-dot"></span>Velbrantix</div>
  <div class="back-url">www.velbrantix.com</div>
</section>

<section class="card card-front">
  <svg class="wave" width="760" height="434" viewBox="0 0 760 434">
    <path d="M0,372 C180,392 340,330 470,250 C580,180 680,150 760,138 L760,160 C680,172 590,200 480,268 C350,350 190,402 0,392 Z" fill="var(--blue-mid)"/>
    <path d="M0,404 C190,420 360,350 490,268 C590,206 680,178 760,170 L760,434 L0,434 Z" fill="var(--blue-deep)"/>
    <path d="M0,398 C190,414 355,344 486,262 C588,200 680,172 760,164" stroke="var(--paper)" stroke-width="4" fill="none"/>
    <path d="M0,418 C210,430 380,360 505,280" stroke="var(--blue-mid)" stroke-width="3" fill="none" opacity="0.8"/>
  </svg>

  <div class="brand"><span class="brand-dot"></span>Velbrantix</div>

  <div class="person">
    <div class="person-name">Your Name</div>
    <div class="person-title">Title</div>
  </div>

  <ul class="contact">
    <li><svg viewBox="0 0 16 16"><path d="M3 1h3l1 4-2 1c1 2 3 4 5 5l1-2 4 1v3c0 1-1 2-2 2C7 15 1 9 1 3c0-1 1-2 2-2z"/></svg>012-345-6789</li>
    <li><svg viewBox="0 0 16 16"><path d="M4 0h8a1 1 0 0 1 1 1v14a1 1 0 0 1-1 1H4a1 1 0 0 1-1-1V1a1 1 0 0 1 1-1zm1 2v10h6V2z"/></svg>012-345-6789</li>
    <li><svg viewBox="0 0 16 16"><path d="M1 3h14v10H1z M1 3l7 6 7-6" stroke="#0792cd" stroke-width="1"/></svg>info@velbrantix.com</li>
    <li><svg viewBox="0 0 16 16"><circle cx="8" cy="8" r="7"/><path d="M1 8h14M8 1v14" stroke="#0792cd" stroke-width="1"/></svg>www.velbrantix.com</li>
  </ul>

  <div class="address">
    <svg viewBox="0 0 16 16"><path d="M8 0a6 6 0 0 1 6 6c0 4-6 10-6 10S2 10 2 6a6 6 0 0 1 6-6zm0 4a2 2 0 1 0 0 4 2 2 0 0 0 0-4z"/></svg>
    Street Name, City Name, Zipcode-012345
  </div>
</section>

</body>
</html>
```